New Year's card HTML

can you produce a best new years wishes 2018 design in HTML for our website as what I would like to send by email towards my network of candidates / customers ...

It must be wow, inspiring , design, meaningfull... MMM those people care about me, or those people will help me to go the extra mile, to help me to achieve my career goals, Your best move, enhance my possibilities, bring the love back

Target Market(s)

CEo's / CMO's/ HRDirectors network of 450k

Coding

Coded - Design and coding required

Number of Pages Required

1 page

Colors

Designer to choose colors to be used in the design.

Requirements
Must have
• Logo / visual / website adress www.moravintel.com and a call to action
Should not have
• no sound as our business is confidential

```html
<!DOCTYPE html>
<html lang="en">
<head>
<meta charset="utf-8">
<title>Happy New Year 2018 – Moravintel</title>
<link rel="stylesheet" href="https://fonts.googleapis.com/css2?family=Lobster&family=Teko:wght@600&family=Cormorant+Garamond:wght@500&display=swap">
<style>
  :root {
    --sky-top: #141830;
    --sky-mid: #262c4c;
    --sky-glow: #5a3c4c;
    --burst-gold: 240, 214, 170;
    --burst-pink: 214, 90, 120;
    --burst-blue: 110, 140, 235;
    --burst-amber: 230, 150, 90;
    --band-dark: #1c1426;
    --band-red: #b9434c;
    --band-pink: #d48a92;
    --white: #ffffff;
    --muted-white: #e6dfe6;
    --button-dark: #1a1a1a;
    --button-rim-light: #f2f2f2;
    --button-rim-dark: #8c8c8c;
  }
  * { margin: 0; padding: 0; box-sizing: border-box; }
  html, body {
    width: 1200px;
    height: 657px;
    overflow: hidden;
    background: var(--band-dark);
  }
  .card {
    position: relative;
    width: 1200px;
    height: 657px;
    overflow: hidden;
  }
  .card__photo {
    position: absolute;
    inset: 0;
    background:
      radial-gradient(circle at 640px 160px, rgba(var(--burst-gold), 0.95) 0, rgba(var(--burst-gold), 0.35) 40px, rgba(var(--burst-gold), 0) 160px),
      radial-gradient(circle at 985px 290px, rgba(var(--burst-pink), 0.95) 0, rgba(var(--burst-pink), 0.4) 50px, rgba(var(--burst-pink), 0) 170px),
      radial-gradient(circle at 900px 260px, rgba(var(--burst-pink), 0.7) 0, rgba(var(--burst-pink), 0) 70px),
      radial-gradient(circle at 935px 100px, rgba(var(--burst-amber), 0.8) 0, rgba(var(--burst-amber), 0) 60px),
      radial-gradient(circle at 1010px 110px, rgba(var(--burst-gold), 0.75) 0, rgba(var(--burst-gold), 0) 55px),
      radial-gradient(circle at 790px 340px, rgba(var(--burst-gold), 0.9) 0, rgba(var(--burst-blue), 0.5) 40px, rgba(var(--burst-blue), 0) 140px),
      radial-gradient(circle at 590px 320px, rgba(var(--burst-amber), 0.6) 0, rgba(var(--burst-amber), 0) 70px),
      radial-gradient(circle at 720px 470px, rgba(var(--burst-gold), 0.6) 0, rgba(var(--burst-gold), 0) 60px),
      radial-gradient(circle at 1090px 510px, rgba(var(--burst-gold), 0.55) 0, rgba(var(--burst-gold), 0) 60px),
      radial-gradient(circle at 320px 20px, rgba(var(--burst-pink), 0.7) 0, rgba(var(--burst-pink), 0) 90px),
      radial-gradient(circle at 830px 20px, rgba(var(--burst-amber), 0.6) 0, rgba(var(--burst-amber), 0) 60px),
      radial-gradient(circle at 110px 200px, rgba(var(--burst-pink), 0.4) 0, rgba(var(--burst-pink), 0) 120px),
      radial-gradient(ellipse 360px 140px at 430px 480px, rgba(var(--burst-amber), 0.6) 0, rgba(var(--burst-amber), 0) 100%),
      radial-gradient(ellipse 230px 150px at 230px 480px, rgba(10, 8, 14, 0.95) 0, rgba(10, 8, 14, 0.9) 60%, rgba(10, 8, 14, 0) 100%),
      linear-gradient(180deg, var(--sky-top) 0%, var(--sky-mid) 50%, var(--sky-glow) 82%, var(--sky-top) 100%);
  }
  .greeting {
    position: absolute;
    left: 78px;
    top: 50px;
    color: var(--white);
    font-family: "Lobster", cursive;
    font-weight: 400;
    line-height: 1;
  }
  .greeting__happy {
    display: block;
    font-size: 72px;
    margin-left: 6px;
  }
  .greeting__new-year {
    display: block;
    font-size: 92px;
    margin-top: -4px;
  }
  .greeting__year {
    display: block;
    font-size: 98px;
    margin-top: 4px;
  }
  .cta {
    position: absolute;
    left: 279px;
    top: 248px;
    width: 180px;
    height: 68px;
    border-radius: 34px;
    background: linear-gradient(180deg, var(--button-rim-light) 0%, var(--button-rim-dark) 50%, var(--button-rim-light) 100%);
    padding: 6px;
    text-decoration: none;
    display: block;
  }
  .cta__face {
    display: flex;
    align-items: center;
    justify-content: center;
    width: 100%;
    height: 100%;
    border-radius: 28px;
    background: linear-gradient(180deg, #444 0%, var(--button-dark) 55%, #2a2a2a 100%);
    color: var(--white);
    font-family: "Teko", sans-serif;
    font-weight: 600;
    font-size: 25px;
    letter-spacing: 0.5px;
    padding-top: 4px;
  }
  .footer-wave {
    position: absolute;
    left: 0;
    bottom: 0;
    width: 1200px;
    height: 160px;
  }
  .brand {
    position: absolute;
    left: 745px;
    top: 582px;
    color: var(--white);
    font-family: "Cormorant Garamond", serif;
    font-weight: 500;
    font-size: 40px;
    letter-spacing: 4px;
    line-height: 1;
  }
  .web-address {
    position: absolute;
    left: 748px;
    top: 628px;
    color: var(--muted-white);
    font-family: "Cormorant Garamond", serif;
    font-weight: 500;
    font-size: 17px;
    letter-spacing: 2px;
    line-height: 1;
    text-decoration: none;
  }
</style>
</head>
<body>
  <main class="card">
    <div class="card__photo" role="img" aria-label="Night sky with colourful fireworks and three people in silhouette pointing up at them"></div>

    <h1 class="greeting">
      <span class="greeting__happy">Happy</span>
      <span class="greeting__new-year">New Year</span>
      <span class="greeting__year">2018</span>
    </h1>

    <a class="cta" href="http://www.moravintel.com"><span class="cta__face">VISIT OUR SITE</span></a>

    <svg class="footer-wave" viewBox="0 0 1200 160" aria-hidden="true">
      <path d="M0,20 C110,80 250,96 420,82 C600,66 760,0 910,6 C1050,12 1150,50 1200,72 L1200,160 L0,160 Z" fill="var(--band-red)"/>
      <path d="M0,28 C110,90 250,106 420,90 C600,74 760,10 910,14 C1050,18 1150,56 1200,78 L1200,160 L0,160 Z" fill="var(--band-pink)"/>
      <path d="M0,34 C110,96 250,110 420,94 C600,78 760,16 910,20 C1050,24 1150,60 1200,82 L1200,160 L0,160 Z" fill="var(--band-dark)"/>
    </svg>

    <div class="brand">MORAVINTEL</div>
    <a class="web-address" href="http://www.moravintel.com">www.moravintel.com</a>
  </main>
</body>
</html>
```